Business card for a new cabinet shop company named Veloran Cabinets for high end cabinets

Design a business card, thinking dark rich green with colours to speak of high end luxury ie; cream, gold, black possibly

Mitchell Tarrowby
Director Craftsman
Email: info@veloranjoinery-example.com.au
Instagram : @veloran.cabinets

```html
<!DOCTYPE html>
<html lang="en">
<head>
<meta charset="utf-8">
<title>Veloran Cabinets – Business Card</title>
<link rel="stylesheet" href="https://fonts.googleapis.com/css2?family=Montserrat:wght@300;400;500;800&display=swap">
<style>
  :root {
    --backdrop: #1c1f1d;
    --card: #12291f;
    --card-edge: #0d1f17;
    --gold: #c9a760;
    --gold-soft: #b3955a;
    --cream: #f1e8d4;
    --cream-muted: #dcd3bf;
  }
  * { margin: 0; padding: 0; box-sizing: border-box; }
  html, body {
    width: 1200px; height: 875px; overflow: hidden;
    background: var(--backdrop);
    font-family: "Montserrat", Arial, sans-serif;
  }
  .canvas {
    position: relative; width: 1200px; height: 875px;
    display: flex; align-items: center; justify-content: center; gap: 50px;
  }
  .card {
    position: relative; width: 525px; height: 300px;
    background: linear-gradient(135deg, var(--card) 0%, var(--card-edge) 100%);
    border-radius: 18px;
    box-shadow: 0 18px 40px rgba(0,0,0,.5);
    overflow: hidden;
  }
  .brand { display: flex; align-items: center; }
  .brand-square { flex: none; border: 3px solid var(--gold); }
  .brand-name { color: var(--gold); font-weight: 500; line-height: 1.08; white-space: nowrap; }

  /* Front */
  .card-front .brand {
    position: absolute; inset: 0;
    justify-content: center; gap: 22px;
  }
  .card-front .brand-square { width: 58px; height: 58px; }
  .card-front .brand-name { font-size: 44px; letter-spacing: .5px; }

  /* Back */
  .card-back .layout {
    position: absolute; inset: 0;
    display: flex; align-items: center; justify-content: center; padding-left: 40px;
  }
  .card-back .brand { gap: 12px; }
  .card-back .brand-square { width: 30px; height: 30px; border-width: 2px; }
  .card-back .brand-name { font-size: 20px; }
  .divider { width: 1.5px; height: 96px; background: var(--gold); margin: 0 16px; flex: none; }
  .contact { color: var(--cream); }
  .person-name { font-size: 18px; line-height: 1; white-space: nowrap; }
  .person-first { font-weight: 800; color: var(--cream); }
  .person-last { font-weight: 300; color: var(--gold-soft); }
  .person-role { font-size: 11px; font-weight: 400; color: var(--cream-muted); margin-top: 5px; }
  .contact-list { list-style: none; margin-top: 10px; }
  .contact-list li {
    display: flex; align-items: center; gap: 7px;
    font-size: 10px; font-weight: 400; color: var(--cream-muted);
    margin-top: 5px; white-space: nowrap;
  }
  .contact-icon { width: 11px; height: 11px; flex: none; }
</style>
</head>
<body>
<main class="canvas">
  <section class="card card-front" aria-label="Card front">
    <div class="brand">
      <div class="brand-square"></div>
      <div class="brand-name">Veloran<br>Cabinets</div>
    </div>
  </section>

  <section class="card card-back" aria-label="Card back">
    <div class="layout">
      <div class="brand">
        <div class="brand-square"></div>
        <div class="brand-name">Veloran<br>Cabinets</div>
      </div>
      <div class="divider"></div>
      <div class="contact">
        <p class="person-name"><span class="person-first">Mitchell</span> <span class="person-last">Tarrowby</span></p>
        <p class="person-role">Director Craftsman</p>
        <ul class="contact-list">
          <li>
            <svg class="contact-icon" viewBox="0 0 12 12" aria-hidden="true">
              <rect x="0.5" y="2.5" width="11" height="7" fill="var(--gold)"/>
              <path d="M0.5 2.5 L6 7 L11.5 2.5" fill="none" stroke="var(--card)" stroke-width="1"/>
            </svg>
            info@veloranjoinery-example.com.au
          </li>
          <li>
            <svg class="contact-icon" viewBox="0 0 12 12" aria-hidden="true">
              <circle cx="6" cy="6" r="5.5" fill="var(--gold)"/>
            </svg>
            @veloran.cabinets
          </li>
        </ul>
      </div>
    </div>
  </section>
</main>
</body>
</html>
```